Residential Remodeling Contractor needs updated business card

I need a new design for my business card.
Name of the company is Ridgefell Construction. I need a card that commands presence, strength, integrity. I have been in business for 28 years. I am a Residential Remodeling Contractor that covers all aspects of a residential remodel and build.

```html
<!DOCTYPE html>
<html lang="en">
<head>
<meta charset="utf-8">
<title>Ridgefell Construction – Business Card</title>
<link rel="stylesheet" href="https://fonts.googleapis.com/css2?family=Montserrat:wght@400;500;600;700&display=swap">
<style>
  :root {
    --page: #d8d3cb;
    --card: #e8edf1;
    --card-edge: #cfd6dd;
    --navy: #1c3684;
    --navy-deep: #162c6e;
    --cream: #f1e8dc;
    --line: #efe6d8;
  }
  * { margin: 0; padding: 0; box-sizing: border-box; }
  html, body {
    width: 1200px; height: 887px; overflow: hidden;
    background: var(--page);
    font-family: "Montserrat", Arial, sans-serif;
  }
  .card {
    position: absolute; left: 100px; top: 168px;
    width: 1000px; height: 550px;
    background: var(--card);
    border: 1px solid var(--card-edge);
    border-radius: 22px;
    overflow: hidden;
    box-shadow: 0 18px 40px rgba(40, 40, 50, .18);
  }
  .card-shapes { position: absolute; inset: 0; }
  .emblem-area {
    position: absolute; left: 10px; top: 92px;
    width: 114px; height: 458px;
    background: linear-gradient(180deg, var(--navy) 0%, var(--navy-deep) 100%);
  }
  .wordmark {
    position: absolute; left: 189px; top: 56px;
    color: var(--navy);
    font-weight: 600;
    text-transform: uppercase;
    line-height: 1;
  }
  .wordmark span { display: block; }
  .wordmark .line-one { font-size: 52px; letter-spacing: 1px; }
  .wordmark .line-two { font-size: 37px; letter-spacing: 1px; margin-top: 10px; }
  .tagline {
    position: absolute; right: 58px; top: 214px;
    color: var(--cream);
    font-size: 22px; font-weight: 500;
    letter-spacing: 1.2px;
    text-transform: uppercase;
    transform: rotate(2.6deg);
    transform-origin: right center;
    white-space: nowrap;
  }
  .person { position: absolute; left: 189px; top: 322px; color: var(--cream); }
  .person .name { font-size: 34px; font-weight: 600; letter-spacing: 1.5px; text-transform: uppercase; }
  .person .role { font-size: 20px; font-weight: 400; margin-top: 0; }
  .contact { position: absolute; left: 192px; top: 414px; list-style: none; color: var(--cream); }
  .contact li {
    display: flex; align-items: center; gap: 10px;
    font-size: 22px; height: 29.5px; letter-spacing: .5px;
  }
  .contact svg { width: 18px; height: 18px; flex: none; }
  .address {
    position: absolute; right: 58px; top: 444px;
    color: var(--cream); text-align: right;
    font-size: 22px; line-height: 29.5px; letter-spacing: .5px;
  }
</style>
</head>
<body>
  <div class="card">
    <svg class="card-shapes" viewBox="0 0 1000 550" width="1000" height="550" aria-hidden="true">
      <rect x="128" y="192" width="872" height="358" fill="var(--navy)"/>
      <polygon points="128,228 1000,312 1000,318 128,234" fill="var(--line)"/>
      <polygon points="126,228 132,228 146,550 140,550" fill="var(--line)"/>
    </svg>

    <div class="emblem-area" role="img" aria-label="Lighthouse silhouette emblem"></div>

    <h1 class="wordmark">
      <span class="line-one">Ridgefell</span>
      <span class="line-two">Construction</span>
    </h1>

    <p class="tagline">I have been in business for 28 years</p>

    <div class="person">
      <p class="name">Marcus Delane</p>
      <p class="role">Director</p>
    </div>

    <ul class="contact">
      <li>
        <svg viewBox="0 0 24 24" fill="var(--cream)"><path d="M6.6 2.5l3 3.4-1.8 2.6c1.2 2.8 3.2 5 5.8 6.4l2.6-1.8 3.3 3-1.6 3.4C11 19.8 4.5 13 3.4 4.2z"/></svg>
        <span>(555) 014-2287</span>
      </li>
      <li>
        <svg viewBox="0 0 24 24" fill="none" stroke="var(--cream)" stroke-width="2"><rect x="3" y="5.5" width="18" height="13" rx="1"/><path d="M3.5 6.5l8.5 7 8.5-7"/></svg>
        <span>info@ridgefellbuild.com</span>
      </li>
      <li>
        <svg viewBox="0 0 24 24" fill="none" stroke="var(--cream)" stroke-width="1.8"><circle cx="12" cy="12" r="9"/><ellipse cx="12" cy="12" rx="4" ry="9"/><path d="M3 12h18M5 7h14M5 17h14"/></svg>
        <span>www.ridgefellbuild.com</span>
      </li>
    </ul>

    <address class="address" style="font-style: normal;">
      742 Alder Street<br>
      Fenwick, GA 30999
    </address>
  </div>
</body>
</html>
```